Awesome photographers card for an awesome new business

Double sided business card Black background and silver logo in middle on one side. Details on otherside. please keep it simple

Industry/Entity Type

Photographer

Contact Information for Business Card

Gerald Fenwick
0452817360
GeraldFenwickPhotography47@mailbox.test
www.GeraldFenwickPhotography.test.au
Instagram _Gerald_fenwick

Requirements
Must have
• My logo in Silver
• please use instagram logo instead of "Instagram"

```html
<!DOCTYPE html>
<html lang="en">
<head>
<meta charset="utf-8">
<title>Gerald Fenwick Photography – Business Card</title>
<link href="https://fonts.googleapis.com/css2?family=Roboto:wght@400;500;700&display=swap" rel="stylesheet">
<style>
  :root {
    --stage: #1f1f1f;
    --card-dark: #1c1c1d;
    --card-dark-edge: #151516;
    --silver-light: #f2f2f2;
    --silver-mid: #c9c9cb;
    --silver-deep: #9a9a9c;
    --text-light: #e6e6e6;
    --text-name: #c4c4c4;
    --text-dark: #151515;
    --icon-grey: #9b9b9b;
  }
  * { margin: 0; padding: 0; box-sizing: border-box; }
  html, body { width: 1200px; height: 960px; overflow: hidden; }
  body {
    background: var(--stage);
    font-family: "Roboto", Arial, sans-serif;
    position: relative;
  }
  .card {
    position: absolute;
    width: 600px;
    height: 342px;
    overflow: hidden;
  }
  .card--front {
    left: 314px; top: 113px;
    background: linear-gradient(180deg, var(--card-dark) 0%, var(--card-dark-edge) 100%);
  }
  .card--back {
    left: 311px; top: 472px;
    background: linear-gradient(90deg, var(--silver-deep) 0%, var(--silver-light) 40%, var(--silver-light) 60%, var(--silver-deep) 100%);
  }
  .brand-mark {
    position: absolute;
    border-radius: 50%;
    display: flex;
    flex-direction: column;
    align-items: center;
    justify-content: center;
    text-align: center;
    font-family: "Roboto", Arial, sans-serif;
    font-weight: 500;
    text-transform: uppercase;
    letter-spacing: 2px;
    line-height: 1.35;
  }
  .card--front .brand-mark {
    left: 230px; top: 32px; width: 140px; height: 140px;
    border: 3px solid var(--silver-mid);
    color: var(--silver-mid);
    font-size: 11px;
  }
  .card--back .brand-mark {
    left: 216px; top: 75px; width: 170px; height: 170px;
    border: 3px solid #3a3a3a;
    color: #3a3a3a;
    font-size: 13px;
  }
  .holder-name {
    position: absolute;
    left: 0; right: 0; top: 210px;
    text-align: center;
    font-weight: 700;
    font-size: 20px;
    color: var(--text-name);
    text-transform: uppercase;
  }
  .contact-line {
    position: absolute;
    left: 0; right: 0;
    display: flex;
    justify-content: center;
    align-items: center;
    gap: 6px;
    font-size: 14px;
    color: var(--text-light);
  }
  .contact-line--main { top: 246px; }
  .contact-line--social { top: 265px; }
  .contact-item { display: inline-flex; align-items: center; gap: 4px; }
  .contact-icon { width: 12px; height: 12px; display: block; }
  .social-square { width: 13px; height: 13px; background: var(--icon-grey); display: inline-block; }
  .wave-band { position: absolute; left: 0; top: 286px; width: 600px; height: 56px; }
  .web-front {
    position: absolute; left: 0; right: 0; top: 318px;
    text-align: center; font-size: 14px; line-height: 16px; color: var(--text-dark);
  }
  .web-back {
    position: absolute; left: 0; right: 0; top: 292px;
    text-align: center; font-size: 15px; letter-spacing: 2.2px; color: var(--text-dark);
  }
</style>
</head>
<body>
  <section class="card card--front" aria-label="Business card front">
    <div class="brand-mark">Gerald<br>Fenwick<br>Photography</div>
    <h1 class="holder-name">Gerald Fenwick</h1>
    <div class="contact-line contact-line--main">
      <span class="contact-item">
        <svg class="contact-icon" viewBox="0 0 12 12"><path fill="#9b9b9b" d="M2.4 0.6 4 2.4 3.2 3.9c.7 1.5 1.8 2.6 3.3 3.3L8 6.4l1.8 1.6-.9 2.2C5.3 10 1.8 6.6 1.5 2.6Z"/></svg>
        0452817360
      </span>
      <span class="contact-item">
        <svg class="contact-icon" viewBox="0 0 12 12"><rect x="0.5" y="2.5" width="11" height="7" fill="#9b9b9b"/><path d="M0.5 2.5 6 6.5 11.5 2.5" fill="none" stroke="#1c1c1d" stroke-width="1"/></svg>
        GeraldFenwickPhotography47@mailbox.test
      </span>
    </div>
    <div class="contact-line contact-line--social">
      <span class="contact-item"><span class="social-square"></span>&nbsp;_Gerald_fenwick</span>
    </div>
    <svg class="wave-band" viewBox="0 0 600 56" preserveAspectRatio="none">
      <defs>
        <linearGradient id="bandSilver" x1="0" x2="1" y1="0" y2="0">
          <stop offset="0" stop-color="#8f8f91"/>
          <stop offset="0.5" stop-color="#f0f0f0"/>
          <stop offset="1" stop-color="#8f8f91"/>
        </linearGradient>
      </defs>
      <path d="M0 40 Q300 -18 600 30" fill="none" stroke="#bdbdbd" stroke-width="1.5"/>
      <path d="M0 56 L0 46 Q300 -4 600 40 L600 56 Z" fill="url(#bandSilver)"/>
    </svg>
    <div class="web-front">www.GeraldFenwickPhotography.test.au</div>
  </section>

  <section class="card card--back" aria-label="Business card back">
    <div class="brand-mark">Gerald<br>Fenwick<br>Photography</div>
    <div class="web-back">www.GeraldFenwickPhotography.test.au</div>
  </section>
</body>
</html>
```